One pager digital ad-Corporate travel Manager

I need a design that is smooth, and business like. I don’t like basic generic designs that I can make my self. I’m looking for a sharp clean ad that clearly was made by a great designer. I need some bullet points in and the add to be clean. Here is a list of some content from our content writers. You can arrange and play with the words a bit.

*Budget*- having a travel management service will ensure that your company sticks to a budget which will help PROTECT your bottom line. Travel expenses often CAN BE COSTLY and having a SAVVY corporate travel manager handle YOUR TRAVEL ARRANGEMENTS will make sure that the travel expenses are kept under control.
*Efficiency- time *is money. Have your staff focus on their core business and have the corporate travel manager handle all the logistics for their travel including airfare, hotel cars and events TO MAXIMIZE EFFICIENCY AND KEEP YOUR STAFF FOCUSED ON YOUR CORE BUSINESS

*unforeseen circumstances* – the corporate travel manager handleS any cancellations, missed flights, canceled flights. Quick rebooking, and repositioning, and dealing with getting credits and reimbursement is extremely difficult and time-consuming. The corporate travel manager handles all of that SO YOU CAN CONTINUE ON SCHEDULE WITHOUT SPENDING HOURS REBOOKING AND GETTING CREDIT

Efficient and organized business travel management-help reduce travel expenses, streamline expense reports, optimize booking processes, and make managing the corporate travel experience way easier for all stakeholders involved.

Travel Support

Report on travel spend: In order to optimize their budgets, businesses need to know which departments are spending what on travel. Agencies can report on spend for all stakeholders by team, department, or project, and help you accurately track all your travel expenses.

Maintain compliance: Every company has some sort of rules that make up their travel policy. An agency can enforce these guidelines when booking.

Velnor Trips is a global leader in business travel management services. We drive savings, efficiency and safety to businesses and their travelers all around the world.

If you are looking for a tailored travel management solution, delivering customer service excellence, and a demonstrable return on investment, then you’ve come to the right place

Corporate travel policy compliance
Travel management reports
Meetings and event management
Travel program management
Dedicated travel counselor teams

By listening to your needs and focusing on your goals we can help your company design a global corporate travel service program that controls costs, improves traveler satisfaction and fits your corporate culture.

Our qualified business travel agents and cutting-edge technology deliver solutions that provide the best travel arrangements and travel policy adherence in the business. From CEO to support staff, our services can help make corporate travel a more efficient and enjoyable experience for everyone involved.

With so much involved in travel – from booking and expenses to meetings and strategy – you need the backing of a proven leader…
Velnor Trips, We’re your corporate travel partner to help you manage it all.

```html
<!DOCTYPE html>
<html lang="en">
<head>
<meta charset="utf-8">
<title>Velnor Trips – Corporate Travel Management</title>
<link href="https://fonts.googleapis.com/css2?family=Montserrat:wght@400;500;800;900&display=swap" rel="stylesheet">
<style>
:root{
  --navy:#041a36;
  --ice:#d3f0fb;
  --paper:#ffffff;
}
*{margin:0;padding:0;box-sizing:border-box}
html,body{width:848px;height:1200px;overflow:hidden;background:var(--paper)}
body{font-family:"Montserrat",sans-serif;color:var(--navy);position:relative}
.abs{position:absolute}
.brand{left:0;width:848px;top:32px;text-align:center}
.brand-mark{display:block;margin:0 auto 18px}
.brand-name{font-size:21px;font-weight:400;letter-spacing:4px;line-height:1}
.lead{left:0;width:848px;top:186px;text-align:center;font-size:30px;font-weight:900;line-height:1.1}
.band{left:47px;top:227px;width:765px;height:54px;background:var(--navy);border-radius:4px;color:var(--ice);font-size:33.5px;font-weight:900;text-align:center;line-height:54px;letter-spacing:.2px}
.sub{left:79px;font-size:21.5px;font-weight:900;line-height:1}
.sub-1{top:292px}
.sub-2{top:328px}
.pill{left:355px;top:321px;width:460px;height:35px;background:var(--navy);border-radius:3px;color:var(--ice);font-size:21.5px;font-weight:900;line-height:35px;padding-left:10px}
.intro{left:0;width:848px;top:372px;text-align:center;font-size:15.5px;line-height:20.5px}
.intro b{font-weight:800}
.card{left:53px;width:351px;background:var(--navy);border-radius:14px;color:var(--ice);padding:14px 22px}
.card p{color:#fff;font-size:10.5px;line-height:18px}
.card h2,.section h2{font-size:17px;font-weight:900;letter-spacing:.2px;margin-bottom:3px}
.budget{top:442px;height:181px}
.unforeseen{top:795px;height:202px;padding-top:16px}
.caps{font-weight:800}
.card .caps{font-size:10.2px}
.section{left:75px;top:641px;width:330px}
.section p{font-size:10.5px;line-height:18px}
.perks{left:459px;top:432px;list-style:none}
.perks li{font-size:14.5px;font-weight:900;line-height:26.5px;position:relative;padding-left:19px}
.perks li::before{content:"";position:absolute;left:0;top:8px;width:10px;height:10px;border-radius:50%;background:var(--navy)}
.agents{left:459px;top:575px;width:300px;font-size:10.2px;line-height:14.8px}
.frame{left:433px;top:682px;width:375px;height:93px;border:3px solid var(--navy);border-radius:10px;padding:20px 0 0 23px}
.frame h3{font-size:10.9px;font-weight:900}
.frame p{font-size:10px;line-height:14.5px}
.support{left:459px;top:803px;width:300px}
.support h2{font-size:14.5px;font-weight:900;line-height:19px}
.support h3{font-size:14px;font-weight:900;line-height:18px}
.support p{font-size:10.2px;line-height:14.5px}
.support .gap{margin-top:16px}
.closing{left:0;width:848px;top:1024px;text-align:center;font-size:12.4px;line-height:19.5px}
.closing b{font-weight:900}
.cta-box{left:240px;top:1077px;width:382px;height:39px;border:3px solid var(--navy);text-align:center;font-size:17px;font-weight:900;line-height:33px}
.cta{left:0;width:848px;top:1119px;text-align:center;font-size:17.5px;line-height:23px}
.cta strong{font-weight:900;font-size:16.8px}
</style>
</head>
<body>
<header class="brand abs">
  <svg class="brand-mark" width="92" height="92" viewBox="0 0 92 92" aria-hidden="true"><circle cx="46" cy="46" r="44" fill="none" stroke="#041a36" stroke-width="2"/></svg>
  <div class="brand-name">VELNOR TRIPS</div>
</header>

<h1 class="lead abs">If you are looking for a</h1>
<div class="band abs">Tailored Travel Management Solution,</div>
<div class="sub sub-1 abs">Delivering Customer Service Excellence, and a Demonstrable</div>
<div class="sub sub-2 abs">Return On Investment,</div>
<div class="pill abs">then you’ve come to the right place.</div>

<p class="intro abs"><b>Velnor Trips</b> is a global leader in business travel management services.<br>We drive savings, efficiency and safety to businesses and their travelers all around the world.</p>

<section class="card budget abs">
  <h2>BUDGET</h2>
  <p>Having a travel management service will ensure that<br>your company sticks to a budget which will help<br>PROTECT your bottom line.<br>Travel expenses often CAN BE COSTLY<br>and having a SAVVY corporate travel manager handle<br>YOUR TRAVEL ARRANGEMENTS will make sure<br>that the travel expenses are kept under control.</p>
</section>

<section class="section abs">
  <h2>EFFICIENCY</h2>
  <p><b class="caps">Time is money.</b> Have your staff focus on their<br>core business and have the corporate travel manager<br>handle all the logistics for their travel including<br>airfare, hotel cars and events<br><span class="caps">TO MAXIMIZE EFFICIENCY AND KEEP YOUR STAFF<br>FOCUSED ON YOUR CORE BUSINESS.</span></p>
</section>

<section class="card unforeseen abs">
  <h2>UNFORESEEN CIRCUMSTANCES</h2>
  <p>The corporate travel manager handles any<br>cancellations, missed flights, canceled flights.<br>Quick rebooking, and repositioning, and dealing<br>with getting credits and reimbursement is extremely<br>difficult and time-consuming.<br>The corporate travel manager handles all of that<br><span class="caps">SO YOU CAN CONTINUE ON SCHEDULE WITHOUT<br>SPENDING HOURS REBOOKING AND GETTING CREDIT.</span></p>
</section>

<ul class="perks abs">
  <li>Corporate travel policy compliance</li>
  <li>Travel management reports</li>
  <li>Meetings and event management</li>
  <li>Travel program management</li>
  <li>Dedicated travel counselor teams</li>
</ul>

<p class="agents abs">Our qualified business travel agents and cutting-edge<br>technology deliver solutions that provide the best travel<br>arrangements and travel policy adherence in the business.<br>From CEO to support staff, our services can help make<br>corporate travel a more efficient and enjoyable experience<br>for everyone involved.</p>

<div class="frame abs">
  <h3>Efficient And Organized Business Travel Management</h3>
  <p>help reduce travel expenses, streamline expense reports,<br>optimize booking processes, and make managing the corporate<br>travel experience way easier for all stakeholders involved.</p>
</div>

<section class="support abs">
  <h2>TRAVEL SUPPORT</h2>
  <h3>Report on travel spend:</h3>
  <p>In order to optimize their budgets, businesses need<br>to know which departments are spending what on travel.<br>Agencies can report on spend for all stakeholders by team,<br>department, or project, and help you accurately<br>track all your travel expenses.</p>
  <h3 class="gap">Maintain compliance:</h3>
  <p>Every company has some sort of rules that make up their<br>travel policy.<br>An agency can enforce these guidelines when booking.</p>
</section>

<p class="closing abs"><b>By listening to your needs and focusing on your goals</b> we can help your company design a global corporate travel<br>service program that controls costs, improves traveler satisfaction and fits your corporate culture.</p>

<div class="cta-box abs">WITH SO MUCH INVOLVED IN TRAVEL</div>
<p class="cta abs">from booking and expenses to meetings and strategy,<br>you need the backing of a proven leader…<br><strong>Velnor Trips, we’re your corporate travel partner to help you manage it all.</strong></p>
</body>
</html>
```